sydney wedding photography business needs a business card design

we need a business card design for a sydney based wedding photography and videography business. our business name is :golden hour studio and film. our target clients are 24-35 yrs female. our style is candid, organic, natural, dynamic. we are a team of young photographers and videographers, and help brides to create memories that they will cherish for the rest of their lives. the logo will be provided. we want an elegant design that reflects our style, and also want to give a great impression to our clients that we are one of the best studios in sydney and our brand means quality and premium service.

Target Market(s)

bride to be, 24-35 years old, living in sydney and surrunding areas

Industry/Entity Type

Wedding Photography

Contact Information for Business Card

address: 57 tarrant street, glenmore nsw 2047
mobile: 0431872259
phone: (02) 9163 2408
info@tidewillowstudio.net.au
www.tidewillowstudio.net.au
facebook:tidewillowweddings
instagram:tidewillowweddings

Font styles to use
Serif
Sans Serif

Requirements
Nice to have
• maybe add my slogan"memories beyond eternity" if the layout looks good
Should not have
• no black color, not good idea for wedding biz card

```html
<!DOCTYPE html>
<html lang="en">
<head>
<meta charset="utf-8">
<title>Golden Hour Studio and Film – Business Card</title>
<link href="https://fonts.googleapis.com/css2?family=Arimo:wght@400;700&display=swap" rel="stylesheet">
<style>
  :root {
    --backdrop: #e4ddd2;
    --card: #f8f3ea;
    --card-edge: #fffbf4;
    --gold: #b3841a;
    --ink: #3b3229;
    --muted: #6e6256;
  }
  * { box-sizing: border-box; margin: 0; padding: 0; }
  html, body {
    width: 1200px;
    height: 843px;
    overflow: hidden;
    background: var(--backdrop);
    font-family: "Arimo", Arial, sans-serif;
  }
  .canvas {
    width: 1200px;
    height: 843px;
    display: flex;
    align-items: center;
    justify-content: center;
    gap: 44px;
  }
  .card {
    position: relative;
    width: 540px;
    height: 330px;
    background: linear-gradient(160deg, var(--card-edge) 0%, var(--card) 60%);
    box-shadow: 0 14px 34px rgba(80, 60, 30, 0.22);
  }

  /* Back of card: brand name centred */
  .card--back {
    display: flex;
    align-items: center;
    justify-content: center;
    gap: 14px;
  }
  .brand-dot {
    flex: none;
    width: 14px;
    height: 14px;
    border-radius: 50%;
    background: var(--gold);
  }
  .brand-name {
    color: var(--gold);
    font-weight: 700;
    font-size: 27px;
    letter-spacing: 0.5px;
    white-space: nowrap;
  }

  /* Front of card: brand at right, contact details lower left */
  .brand-corner {
    position: absolute;
    right: 30px;
    top: 56px;
    display: flex;
    align-items: center;
    gap: 8px;
  }
  .brand-corner .brand-dot { width: 12px; height: 12px; }
  .brand-corner .brand-name { font-size: 16px; letter-spacing: 0.3px; }

  .contact {
    position: absolute;
    left: 30px;
    top: 118px;
    color: var(--ink);
  }
  .contact__name {
    color: var(--gold);
    font-size: 21px;
    font-weight: 400;
    line-height: 1.1;
  }
  .contact__role {
    font-size: 15px;
    color: var(--muted);
    margin-bottom: 16px;
  }
  .contact__line {
    font-size: 15px;
    line-height: 1.5;
    letter-spacing: 0.1px;
    white-space: nowrap;
  }
  .contact__label { color: var(--gold); }
  .contact__gap { display: inline-block; width: 10px; }

  .rule {
    position: absolute;
    left: 30px;
    right: 30px;
    bottom: 54px;
    height: 1.5px;
    background: var(--gold);
  }
</style>
</head>
<body>
  <main class="canvas">
    <section class="card card--back" aria-label="Business card back">
      <span class="brand-dot"></span>
      <span class="brand-name">golden hour studio and film</span>
    </section>

    <section class="card card--front" aria-label="Business card front">
      <div class="brand-corner">
        <span class="brand-dot"></span>
        <span class="brand-name">golden hour studio and film</span>
      </div>
      <div class="contact">
        <p class="contact__name">Liam Hart</p>
        <p class="contact__role">President</p>
        <p class="contact__line">57 tarrant street, glenmore nsw 2047</p>
        <p class="contact__line"><span class="contact__label">P :</span> (02) 9163 2408<span class="contact__gap"></span><span class="contact__label">M :</span> (04) 3187 2259</p>
        <p class="contact__line"><span class="contact__label">E :</span> info@tidewillowstudio.net.au<span class="contact__gap"></span><span class="contact__label">W :</span> tidewillowstudio.net.au</p>
      </div>
      <div class="rule"></div>
    </section>
  </main>
</body>
</html>
```